Pellham Grove Trust - New Website Designed

I need a site that looks like this http://www.quorlandgiving.org for boat donations. So please replace the cars with boats.

```html
<!DOCTYPE html>
<html lang="en">
<head>
<meta charset="utf-8">
<title>Pellham Grove Trust — Donate Your Boat</title>
<link href="https://fonts.googleapis.com/css2?family=Lato:wght@400;700;900&family=Tinos:wght@700&display=swap" rel="stylesheet">
<style>
:root{
  --navy:#10288a;
  --navy-deep:#0b1f6e;
  --red:#b80e10;
  --red-dark:#9c0a0c;
  --ink:#333;
  --muted:#8a8a8a;
  --line:#e2e2e2;
  --paper:#fff;
  --soft:#f3f3f3;
}
*{box-sizing:border-box;margin:0;padding:0}
html,body{width:1200px;height:2894px;overflow:hidden;background:var(--paper)}
body{position:relative;font-family:"Lato",Arial,sans-serif;color:var(--ink)}
.abs{position:absolute}

/* header */
.top-rule{left:0;top:0;width:1200px;height:4px;background:var(--navy)}
.brand{left:100px;top:42px;display:flex;align-items:center;gap:14px}
.brand-square{width:30px;height:30px;background:var(--red)}
.brand-name{font-weight:900;font-size:25px;line-height:1.05;color:var(--navy);width:200px;text-transform:uppercase}
.nav{left:0;top:131px;width:1200px;height:52px;background:var(--navy)}
.nav ul{list-style:none;display:flex;gap:34px;position:absolute;left:99px;top:17px}
.nav li{color:#fff;font-size:14px;font-weight:700;letter-spacing:.2px}

/* call + form */
.call-box{left:735px;top:0;width:365px;height:120px;background:var(--red);color:#fff}
.call-icon{position:absolute;left:34px;top:28px;width:52px;height:52px;border-radius:50%;background:#fff}
.call-text{position:absolute;left:98px;top:22px;font-family:"Tinos",serif}
.call-text .k{font-size:15px}
.call-text .n{font-size:21px;margin:5px 0 4px}
.call-text .s{font-size:13px}
.form-tab{left:735px;top:120px;width:365px;height:60px;background:#fff;color:var(--red);font-weight:900;font-size:26px;text-align:center;line-height:60px}
.form-panel{left:735px;top:180px;width:365px;height:518px;background:var(--red);color:#fff}
.form-badge{position:absolute;left:156px;top:20px;width:54px;height:54px;border-radius:50%;background:var(--red-dark);border:2px solid #d43a3c}
.form-panel h3{position:absolute;left:27px;font-size:17px;font-weight:700}
.field{position:absolute;left:27px;width:311px;height:38px;background:#fff;border-radius:4px;color:#9a9a9a;font-size:12px;padding:12px 18px}
.field.half{width:153px}
.field .chev{position:absolute;right:14px;top:11px}
.donate-btn{position:absolute;left:27px;top:451px;width:311px;height:39px;background:var(--navy-deep);color:#fff;font-size:15px;font-weight:700;letter-spacing:1.5px;text-align:center;line-height:39px}

/* hero */
.hero{left:0;top:183px;width:735px;height:515px;background:linear-gradient(160deg,#e7eaee 0%,#c9ced4 45%,#8b8d78 75%,#6e6e5a 100%)}

/* benefits band */
.benefits{left:0;top:698px;width:1200px;height:251px;background:var(--soft)}
.benefits svg.lead{position:absolute;left:0;top:0}
.lead-text{position:absolute;left:96px;top:66px;color:#fff}
.lead-text .a{font-size:22px}
.lead-text .b{font-size:40px;font-weight:900;margin:12px 0 8px}
.lead-text .c{font-size:22px}
.benefit{position:absolute;top:46px;width:160px;text-align:center;font-size:15px;color:#333;line-height:1.5}
.benefit svg{display:block;margin:0 auto 14px}

/* section titles */
.sec-title{left:0;width:1200px;text-align:center;font-size:30px;color:var(--navy);font-weight:400}
.sec-title span{color:var(--red)}
.sec-title::before,.sec-title::after{content:"";display:inline-block;width:180px;height:1px;background:var(--line);vertical-align:middle;margin:0 40px}

/* steps */
.step{position:absolute;top:1122px;width:260px;text-align:center}
.step .ring{width:188px;height:188px;margin:0 auto;border-radius:50%;border:5px solid var(--red);display:flex;align-items:center;justify-content:center}
.step .inner{width:158px;height:158px;border-radius:50%;border:2px dashed #d9d9d9;display:flex;align-items:center;justify-content:center}
.step h4{font-size:19px;font-weight:400;color:#333;margin-top:30px}
.step p{font-size:13.5px;color:var(--muted);line-height:1.7;margin-top:14px}

/* why */
.why{left:0;top:1499px;width:1200px;height:409px;background:var(--navy)}
.why-photo{position:absolute;left:0;top:0;width:660px;height:409px;background:linear-gradient(180deg,#a9c7e3 0%,#d9e6ef 38%,#2d6aa8 62%,#0d3f7c 100%)}
.why h2{position:absolute;left:685px;top:58px;color:#fff;font-size:26px;font-weight:400}
.why h2 span{color:var(--red)}
.why ul{position:absolute;left:685px;top:114px;list-style:none}
.why li{color:#fff;font-size:13px;font-weight:700;height:36px;display:flex;align-items:center;gap:20px}
.why li svg{flex:none}

/* faq */
.faq-photo{left:135px;top:2083px;width:310px;height:415px;background:linear-gradient(180deg,#fff 0%,#c7c2b4 30%,#8e8a79 65%,#6e6c5f 100%);border-radius:120px 120px 0 0}
.acc{left:478px;width:622px}
.acc-active{top:2093px;height:149px;border:1px solid var(--line);border-radius:4px}
.acc-active .head{height:41px;background:var(--red);color:#fff;font-size:13px;font-weight:700;padding:13px 28px;border-radius:4px 4px 0 0;position:relative}
.acc-active p{font-size:13px;color:var(--muted);line-height:1.85;padding:14px 28px}
.acc-item{height:42px;border:1px solid var(--line);border-radius:4px;font-size:13px;color:#777;padding:13px 28px}
.acc .sym{position:absolute;right:26px;top:13px}

/* footer */
.footer{left:0;top:2498px;width:1200px;height:396px;background:linear-gradient(135deg,#1b3ca6 0%,#10288a 60%,#0d2275 100%);color:#fff}
.footer .brand-name{color:#fff;font-size:28px;width:190px}
.f-brand{position:absolute;left:100px;top:134px;display:flex;align-items:center;gap:14px}
.f-divider{position:absolute;left:386px;top:90px;width:1px;height:140px;background:rgba(255,255,255,.25)}
.quick{position:absolute;left:442px;top:72px}
.quick h5{font-size:17px;font-weight:400;margin-bottom:20px}
.quick li{list-style:none;font-size:13px;height:31px}
.f-call{position:absolute;left:690px;top:73px;width:410px;height:143px;border:2px solid rgba(255,255,255,.85);border-radius:4px}
.f-call .ring{position:absolute;left:36px;top:40px;width:62px;height:62px;border-radius:50%;border:2px solid #fff;display:flex;align-items:center;justify-content:center}
.f-call .txt{position:absolute;left:122px;top:34px;font-family:"Tinos",serif}
.f-call .k{font-size:20px}
.f-call .n{font-size:21px;color:var(--red);margin:6px 0}
.f-call .s{font-size:14px}
.f-rule{position:absolute;left:100px;top:299px;width:1000px;height:1px;background:rgba(255,255,255,.2)}
.copy{position:absolute;left:100px;top:342px;font-size:12.5px}
.social{position:absolute;left:940px;top:336px;display:flex;gap:14px}
.social i{display:block;width:30px;height:30px;background:#fff;opacity:.9}
</style>
</head>
<body>

<div class="abs top-rule"></div>

<header>
  <div class="abs brand"><div class="brand-square"></div><div class="brand-name">Pellham Grove Trust</div></div>
  <nav class="abs nav"><ul><li>HOME</li><li>HOW TO DONATE</li><li>ABOUT</li><li>WHY DONATE</li><li>FAQ</li></ul></nav>
</header>

<div class="abs hero" role="img" aria-label="Photo of a soldier carrying a child with a flag, pointing toward a white motor yacht"></div>

<aside>
  <div class="abs call-box">
    <div class="call-icon">
      <svg width="52" height="52" viewBox="0 0 52 52"><path d="M19 15c2 0 3 4 4 6 0 2-3 3-2 5 1 3 3 5 6 6 2 1 3-2 5-2 2 1 6 2 6 4 0 3-3 5-6 5-10-1-18-9-19-19 0-3 3-5 6-5z" fill="#b80e10"/></svg>
    </div>
    <div class="call-text"><div class="k">CALL TODAY TO DONATE</div><div class="n">1-800-555-0147</div><div class="s">Live Operators Available - 7 Days A Week</div></div>
  </div>
  <div class="abs form-tab">Donation PickUp Form</div>
  <div class="abs form-panel">
    <div class="form-badge">
      <svg width="50" height="50" viewBox="0 0 50 50"><path d="M25 13v16h-9zM27 16l8 13h-8z" fill="#fff"/><path d="M13 31h24l-4 6H17z" fill="#fff"/></svg>
    </div>
    <h3 style="top:96px">DONATE YOUR BOATS ONLINE</h3>
    <div class="field" style="top:134px">Enter Name</div>
    <div class="field" style="top:177px">Zip Code</div>
    <div class="field" style="top:221px">Day Phone</div>
    <div class="field" style="top:264px">Email Address</div>
    <h3 style="top:330px;font-weight:400">Donation Information</h3>
    <div class="field half" style="top:366px">Choose Year<svg class="chev" width="10" height="10" viewBox="0 0 10 10"><path d="M2 3l3 3 3-3" stroke="#999" fill="none" stroke-width="1.4"/></svg></div>
    <div class="field half" style="top:366px;left:185px">Choose Make<svg class="chev" width="10" height="10" viewBox="0 0 10 10"><path d="M2 3l3 3 3-3" stroke="#999" fill="none" stroke-width="1.4"/></svg></div>
    <div class="field" style="top:409px">Model of Vehicle</div>
    <div class="donate-btn">DONATE NOW !</div>
  </div>
</aside>

<section class="abs benefits">
  <svg class="lead" width="470" height="251" viewBox="0 0 470 251"><path d="M0 0H372L460 125 372 251H0z" fill="#0d2b8a"/><path d="M372 0h10l88 125-88 126h-10l88-126z" fill="#3d5cc0"/></svg>
  <div class="lead-text"><div class="a">DONATE YOUR BOATS TO</div><div class="b">VETERANS</div><div class="c">MAKE A DIFFERENCE</div></div>

  <div class="benefit" style="left:474px">
    <svg width="100" height="96" viewBox="0 0 100 96"><polygon points="50,0 61.8,35.1 98.5,35.1 68.8,56.8 80.2,91.9 50,70 19.8,91.9 31.2,56.8 1.5,35.1 38.2,35.1" fill="#b80e10"/><circle cx="50" cy="50" r="11" fill="#fff"/><path d="M44 50l4 4 8-8" stroke="#b80e10" stroke-width="3" fill="none"/></svg>
    You have no costs</div>
  <div class="benefit" style="left:638px">
    <svg width="100" height="96" viewBox="0 0 100 96"><polygon points="50,0 61.8,35.1 98.5,35.1 68.8,56.8 80.2,91.9 50,70 19.8,91.9 31.2,56.8 1.5,35.1 38.2,35.1" fill="#b80e10"/><path d="M36 42h14v12H36zM50 46h8l5 6v2H50z" fill="#fff"/><circle cx="41" cy="56" r="3" fill="#fff"/><circle cx="58" cy="56" r="3" fill="#fff"/></svg>
    Free towing,<br>running or not</div>
  <div class="benefit" style="left:804px">
    <svg width="100" height="96" viewBox="0 0 100 96"><polygon points="50,0 61.8,35.1 98.5,35.1 68.8,56.8 80.2,91.9 50,70 19.8,91.9 31.2,56.8 1.5,35.1 38.2,35.1" fill="#b80e10"/><path d="M41 38h13l6 6v18H41z" fill="#fff"/><path d="M45 48h10M45 52h10M45 56h10" stroke="#b80e10" stroke-width="1.5"/></svg>
    We issue you an<br>IRS tax receipt</div>
  <div class="benefit" style="left:968px">
    <svg width="100" height="96" viewBox="0 0 100 96"><polygon points="50,0 61.8,35.1 98.5,35.1 68.8,56.8 80.2,91.9 50,70 19.8,91.9 31.2,56.8 1.5,35.1 38.2,35.1" fill="#b80e10"/><path d="M41 38h13l6 6v18H41z" fill="#fff"/><rect x="46" y="48" width="9" height="9" fill="none" stroke="#b80e10" stroke-width="1.5"/></svg>
    We take care of<br>all paperwork</div>
</section>

<h2 class="abs sec-title" style="top:1028px">HOW TO <span>DONATE</span></h2>

<section>
  <div class="step" style="left:117px">
    <div class="ring"><div class="inner">
      <svg width="70" height="70" viewBox="0 0 70 70"><rect x="12" y="8" width="38" height="52" rx="3" fill="none" stroke="#10288a" stroke-width="4"/><path d="M20 22h22M20 31h22M20 40h14" stroke="#10288a" stroke-width="4"/><path d="M44 50l16-20 5 4-16 20-7 3z" fill="#10288a"/></svg>
    </div></div>
    <h4>Call Or Fill Form</h4>
    <p>Donating your vehicle is easy and<br>donation is accepted nationwide.</p>
  </div>
  <svg class="abs" style="left:360px;top:1190px" width="130" height="70" viewBox="0 0 130 70"><path d="M8 58C40 70 80 55 110 18" stroke="#d8d8d8" stroke-width="5" fill="none"/><path d="M94 14l22-4-4 22z" fill="#d8d8d8"/></svg>
  <div class="step" style="left:468px">
    <div class="ring"><div class="inner">
      <svg width="96" height="70" viewBox="0 0 96 70"><path d="M6 14l22 22" stroke="#10288a" stroke-width="5"/><rect x="20" y="30" width="40" height="20" fill="#10288a"/><path d="M60 22h16l12 14v14H60z" fill="#10288a"/><path d="M65 27h9l7 8H65z" fill="#fff"/><circle cx="32" cy="54" r="8" fill="#10288a" stroke="#fff" stroke-width="3"/><circle cx="74" cy="54" r="8" fill="#10288a" stroke="#fff" stroke-width="3"/></svg>
    </div></div>
    <h4>We Tow Boat Free</h4>
    <p>Donate you vehicle and arrange for<br>easy pick-up and free towing.</p>
  </div>
  <svg class="abs" style="left:712px;top:1190px" width="130" height="70" viewBox="0 0 130 70"><path d="M8 30C40 2 90 8 112 48" stroke="#d8d8d8" stroke-width="5" fill="none"/><path d="M98 46l20 10 0-22z" fill="#d8d8d8"/></svg>
  <div class="step" style="left:815px">
    <div class="ring"><div class="inner">
      <svg width="70" height="80" viewBox="0 0 70 80"><path d="M12 6h32l16 16v52H12z" fill="none" stroke="#10288a" stroke-width="4"/><path d="M44 6v16h16" fill="none" stroke="#10288a" stroke-width="4"/><rect x="18" y="42" width="36" height="20" rx="2" fill="#10288a"/><text x="36" y="57" fill="#fff" font-family="Lato,sans-serif" font-size="13" font-weight="700" text-anchor="middle">TAX</text></svg>
    </div></div>
    <h4>Tax Write Off</h4>
    <p>You will receive your tax deductible<br>vehicle donation receipt.</p>
  </div>
</section>

<section class="abs why">
  <div class="why-photo" role="img" aria-label="Photo of a white motor yacht cruising on open blue water"></div>
  <svg class="abs" style="left:520px;top:0" width="160" height="409" viewBox="0 0 160 409"><path d="M20 0H140L160 409H120z" fill="#10288a"/><path d="M20 0h10l100 409h-10z" fill="#b80e10"/></svg>
  <h2>WHY DONATE YOUR <span>BOATS TO US</span></h2>
  <ul>
    <li><svg width="14" height="14" viewBox="0 0 14 14"><circle cx="7" cy="7" r="7" fill="#fff"/><path d="M6 4l3 3-3 3" stroke="#10288a" stroke-width="2" fill="none"/></svg>Lorem ipsum dolor sit amet consectetur adipiscing elit</li>
    <li><svg width="14" height="14" viewBox="0 0 14 14"><circle cx="7" cy="7" r="7" fill="#fff"/><path d="M6 4l3 3-3 3" stroke="#10288a" stroke-width="2" fill="none"/></svg>Sed do eiusmod tempor incididunt ut labore et dolore</li>
    <li><svg width="14" height="14" viewBox="0 0 14 14"><circle cx="7" cy="7" r="7" fill="#fff"/><path d="M6 4l3 3-3 3" stroke="#10288a" stroke-width="2" fill="none"/></svg>Magna aliquatnim ad minim veniamquis nostrud exercitation</li>
    <li><svg width="14" height="14" viewBox="0 0 14 14"><circle cx="7" cy="7" r="7" fill="#fff"/><path d="M6 4l3 3-3 3" stroke="#10288a" stroke-width="2" fill="none"/></svg>Ullamco laboris nisi ut aliquip ex ea commodo consequat</li>
    <li><svg width="14" height="14" viewBox="0 0 14 14"><circle cx="7" cy="7" r="7" fill="#fff"/><path d="M6 4l3 3-3 3" stroke="#10288a" stroke-width="2" fill="none"/></svg>Duis aute irure dolor in reprehenderit in voluptate velit</li>
    <li><svg width="14" height="14" viewBox="0 0 14 14"><circle cx="7" cy="7" r="7" fill="#fff"/><path d="M6 4l3 3-3 3" stroke="#10288a" stroke-width="2" fill="none"/></svg>Ecat cupidatat non proident sunt in culpa qui officia deserunt</li>
    <li><svg width="14" height="14" viewBox="0 0 14 14"><circle cx="7" cy="7" r="7" fill="#fff"/><path d="M6 4l3 3-3 3" stroke="#10288a" stroke-width="2" fill="none"/></svg>Mollit anim id est laborum</li>
  </ul>
</section>

<h2 class="abs sec-title" style="top:1990px">FREQUENTLY ASKED <span>QUESTIONS</span></h2>

<section>
  <div class="abs faq-photo" role="img" aria-label="Photo of a smiling soldier in camouflage hugging his young daughter"></div>
  <div class="abs acc acc-active">
    <div class="head">Lorem ipsum doloconsectetur adipiscing
      <svg class="sym" width="14" height="14" viewBox="0 0 14 14"><circle cx="7" cy="7" r="7" fill="#fff"/><path d="M4 7h6" stroke="#b80e10" stroke-width="2"/></svg></div>
    <p>Sed ut perspiciatis unde omnis iste natus error sit voluptatem accusantium doloremque laudantiumtotam rem aperiam, eaque ipsa quae avelit esse cillum dolore eu fugiat nulla pariat unde omnis iste natus error.</p>
  </div>
  <div class="abs acc acc-item" style="top:2253px">Sed do eiusmod tempor incididunt ut labore ?<svg class="sym" width="14" height="14" viewBox="0 0 14 14"><circle cx="7" cy="7" r="7" fill="#888"/><path d="M4 7h6M7 4v6" stroke="#fff" stroke-width="2"/></svg></div>
  <div class="abs acc acc-item" style="top:2299px">Excepteur sint occaecat cupidatatproidene ?<svg class="sym" width="14" height="14" viewBox="0 0 14 14"><circle cx="7" cy="7" r="7" fill="#888"/><path d="M4 7h6M7 4v6" stroke="#fff" stroke-width="2"/></svg></div>
  <div class="abs acc acc-item" style="top:2346px">Sed do eiusmod tempor incididunt ut labore ?<svg class="sym" width="14" height="14" viewBox="0 0 14 14"><circle cx="7" cy="7" r="7" fill="#888"/><path d="M4 7h6M7 4v6" stroke="#fff" stroke-width="2"/></svg></div>
  <div class="abs acc acc-item" style="top:2392px">Excepteur sint occaecat cupidatatproidene ?<svg class="sym" width="14" height="14" viewBox="0 0 14 14"><circle cx="7" cy="7" r="7" fill="#888"/><path d="M4 7h6M7 4v6" stroke="#fff" stroke-width="2"/></svg></div>
</section>

<footer class="abs footer">
  <div class="f-brand"><div class="brand-square"></div><div class="brand-name">Pellham Grove Trust</div></div>
  <div class="f-divider"></div>
  <div class="quick"><h5>QUICK LINKS</h5><ul><li>Home</li><li>About Us</li><li>How To Donate</li><li>Frequently Asked Questions</li></ul></div>
  <div class="f-call">
    <div class="ring"><svg width="30" height="30" viewBox="0 0 52 52"><path d="M19 15c2 0 3 4 4 6 0 2-3 3-2 5 1 3 3 5 6 6 2 1 3-2 5-2 2 1 6 2 6 4 0 3-3 5-6 5-10-1-18-9-19-19 0-3 3-5 6-5z" fill="#fff"/></svg></div>
    <div class="txt"><div class="k">CALL TODAY TO DONATE</div><div class="n">1-800-555-0147</div><div class="s">Live Operators Available - 7 Days A Week</div></div>
  </div>
  <div class="f-rule"></div>
  <div class="copy">Copyright © Pellham Grove Trust.2017.All rights reserved &nbsp;|&nbsp; Privacy policy</div>
  <div class="social"><i></i><i></i><i></i><i></i></div>
</footer>

</body>
</html>
```